Edgy book cover - contemporary fiction

A book cover design for a first-time author. The book is being self-published, but needs to stand out as a quality product amongst a huge number of self-published titles hitting the market.

About the book
“Pebbles Under Water” is a collection of eleven fictional short stories, set in the the turbulent economic times of The Great Recession (Or the Global Financial Crisis). The stories are about ordinary people and their struggles and hopes, as they cope with the circumstances that are dealt them: losing their jobs and homes, helping friends in trouble, making their own success, having to move across town or across the world to survive, having to go back to work after losing their retirement savings.

The book is being published as an e-book only at this stage. The graphic will be viewed as an icon on the zorbex lumora store (and similar stores such as Plover vreads), and as a larger image on the book's own page. In future, the cover may be used in a print version.

I expect to be challenged and stimulated along the way as I don’t have a firm view of what the final cover will look like – it really is up to you to wow me. I value your time and as such I will commit to giving each designer feedback.

Required Deliverables

Although you need only submit the book cover at the design stage the required project deliverables are:
- Book Front Cover - colour. Main focus
- Other versions once finalised:
- Colour image image 928px wide by 1250px high, at 150ppi,
- B&W image 96ppi B/W, and it will resize automatically to 600px by 800px, which is perfect for the inside Lumora cover.
- 6 by 4 inch postcards and A4 posters for promotional purposes
- Final tag-line applied to all of the above
- Front, back and spine book cover design for future printing of physical book, size 5.25 inches by 8 inches. Zorbex Pagewell template available when number of pages has been finalised.
- At least 2 iterations of the winning design

Target Market(s)

The target for this book is a broad, educated middle-class audience, say over age 30, for whom home, mortgage and job are real concerns.

Industry/Entity Type

Printing

Requirements
Must have
• The cover needs to be edgy but not overdone. Less is more in this case. Think about the target audience and their tastes. I think the title gives lots of creative possibility, so please be creative and clever. I’d like people to look at the cover and think “Cool/Clever cover – I’d better read this”. Be original yet keep the end product accessible.

There will be a tag-line on the cover somewhere. Where you locate it is up to you, but you need to leave space for it. For the time being please use the text “Songs from Narrow Rooms ” – but this may change by the end of the project.

The following text of title, tagline and author

Pebbles Under Water
Songs from Narrow Rooms
Neil Ashbury

Purely as guidance to my taste, some book covers I like are:

http://lnkmo.example/qa1rt
http://lnkmo.example/k4p2z
http://lnkmo.example/bhe7m
http://lnkmo.example/x9dwo
http://lnkmo.example/r3fuy
http://lnkmo.example/j8cns
Should not have
• Please avoid clichés and being “overly busy”. Although the book is to be self published on a low budget it shouldn’t look like that. If the cover would look right on a popular mass fiction title then it is probably not right for me.

The design should not use a cliched "happy families" house image.

It needs not to look like it's based on a book cover template from a self-publishing house.

Some examples of book covers I don’t like are :

http://lnkmo.example/p2gke
http://lnkmo.example/m7ylh
http://lnkmo.example/t5awq
http://lnkmo.example/f1zbv
http://lnkmo.example/d6oxs

```html
<!DOCTYPE html>
<html lang="en">
<head>
<meta charset="utf-8">
<title>Pebbles Under Water — Neil Ashbury</title>
<link rel="stylesheet" href="https://fonts.googleapis.com/css2?family=Jost:wght@200;300&display=swap">
<style>
  :root {
    --paper: #ffffff;
    --frame: #6e6e6e;
    --ink: #1a1a1a;
    --grey: #7a7a7a;
    --tone-light: #d9b7a0;
    --tone-mid: #8f7663;
    --tone-dark: #2f2b24;
  }
  html, body {
    margin: 0;
    padding: 0;
    overflow: hidden;
    background: var(--paper);
  }
  .cover {
    position: relative;
    width: 824px;
    height: 1200px;
    background: var(--paper);
    overflow: hidden;
    font-family: "Jost", "Futura", sans-serif;
  }
  .cover__frame {
    position: absolute;
    left: 50px;
    top: 40px;
    width: 722px;
    height: 1115px;
    border: 1px solid var(--frame);
    box-sizing: border-box;
  }
  .cover__author {
    position: absolute;
    left: 100px;
    top: 68px;
    margin: 0;
    font-weight: 300;
    font-size: 78px;
    letter-spacing: 5px;
    line-height: 1;
    color: var(--grey);
    white-space: nowrap;
  }
  .cover__title {
    position: absolute;
    left: 96px;
    top: 162px;
    margin: 0;
    font-weight: 200;
    font-size: 104px;
    line-height: 0.98;
    text-transform: uppercase;
    color: var(--ink);
    white-space: nowrap;
  }
  .cover__title span { display: block; }
  .cover__tagline {
    position: absolute;
    left: 100px;
    top: 498px;
    margin: 0;
    font-weight: 300;
    font-size: 46px;
    line-height: 1;
    color: var(--grey);
    white-space: nowrap;
    z-index: 2;
  }
  .cover__torn-photo {
    position: absolute;
    left: 0;
    top: 0;
    width: 824px;
    height: 1200px;
    z-index: 1;
  }
</style>
</head>
<body>
  <main class="cover">
    <div class="cover__frame"></div>

    <p class="cover__author">Neil Ashbury</p>

    <h1 class="cover__title">
      <span>Pebbles</span>
      <span>Under Water</span>
    </h1>

    <p class="cover__tagline">Songs from Narrow Rooms</p>

    <svg class="cover__torn-photo" viewBox="0 0 824 1200" role="img"
         aria-label="Photograph of a troubled man holding his head, seen through a torn hole in the white paper">
      <defs>
        <linearGradient id="torn-photo-tone" x1="0" y1="0" x2="1" y2="1">
          <stop offset="0" stop-color="var(--tone-dark)"/>
          <stop offset="0.35" stop-color="var(--tone-mid)"/>
          <stop offset="0.6" stop-color="var(--tone-light)"/>
          <stop offset="1" stop-color="var(--tone-dark)"/>
        </linearGradient>
      </defs>
      <path fill="url(#torn-photo-tone)"
            d="M772 390 L758 396 L742 402 L718 420 L694 440 L668 462 L674 498 L660 526
               L640 548 L604 574 L560 592 L520 604 L486 630 L448 664 L420 700 L398 748
               L378 800 L356 846 L342 892 L326 934 L296 958 L270 1000 L254 1050 L238 1100
               L222 1155 L772 1155 Z"/>
    </svg>
  </main>
</body>
</html>
```